Spring Detox sale graphics for social media

You MUST read the Brief in the WORD document and follow the instructions there. I want to create 10 social media graphics (new Instagram size 4:5 (1080 x 1350 pixels) focusing on our Mother’s Day Spring Detox Sale graphics, using any of the pics attached. Use the attached pics, NO RANDOM STOCK PHOTOGRAPHY. For the color scheme of the graphics, they should all be complementary to the product colors or feel like Spring time.

Target Market(s)

primarily women

Requirements
Must have
• the photos and text attached

```html
<!DOCTYPE html>
<html lang="en">
<head>
<meta charset="utf-8">
<title>Mother's Day Spring Detox Sale – Social Set</title>
<link rel="stylesheet" href="https://fonts.googleapis.com/css2?family=Oswald:wght@300;400;500;600;700&family=Montserrat:wght@500&display=swap">
<style>
  :root{
    --page:#1c1c1c;
    --blush:#fbe4ea;
    --red:#c4262e;
    --maroon:#8a2c33;
    --ink:#262626;
    --plum:#7a2e5e;
    --blue:#2a49a0;
    --forest:#1f4a3c;
    --rose:#c9578f;
    --violet:#3a2d73;
    --mint:#86c6ad;
    --mint-text:#7cc3a6;
    --pink-box:#f5b9bf;
    --pink-band:#f5c2c7;
    --white:#ffffff;
  }
  *{box-sizing:border-box;margin:0;padding:0}
  html,body{width:1200px;height:3119px;overflow:hidden;background:var(--page)}
  body{position:relative;font-family:'Oswald',sans-serif;color:var(--ink)}
  .post{
    position:absolute;width:460px;height:575px;overflow:hidden;
    background:
      radial-gradient(ellipse at 20% 10%,rgba(255,255,255,.85),transparent 55%),
      radial-gradient(ellipse at 80% 95%,rgba(244,180,198,.7),transparent 55%),
      radial-gradient(ellipse at 10% 80%,rgba(250,205,216,.6),transparent 50%),
      var(--blush);
  }
  .col-a{left:131px}.col-b{left:609px}
  .row-1{top:80px}.row-2{top:675px}.row-3{top:1269px}.row-4{top:1867px}.row-5{top:2464px}
  .t{position:absolute;line-height:1;white-space:nowrap}
  .center{left:0;width:460px;text-align:center}
  .deal{position:absolute;display:flex;align-items:flex-start;font-weight:700;line-height:.8}
  .deal .num{font-size:var(--n);letter-spacing:-.03em}
  .deal .side{display:flex;flex-direction:column;margin-left:calc(var(--n)*.02)}
  .deal .sym{font-size:calc(var(--n)*.5);font-weight:600;line-height:.85}
  .deal .off{font-size:calc(var(--n)*.3);font-weight:600;line-height:.9;margin-top:calc(var(--n)*.03)}
  .photo{position:absolute;background:linear-gradient(180deg,#f3eff0,#d9d3d6)}
  .bottles{position:absolute;background:linear-gradient(180deg,#fdfdfd,#e6e3e8 70%,#cdb7cf)}
  .bold{font-weight:700}.semi{font-weight:600}.light{font-weight:300}.reg{font-weight:400}
  .band{position:absolute;left:0;width:460px}
</style>
</head>
<body>

<!-- 1 -->
<section class="post col-a row-1">
  <div class="t bold" style="left:59px;top:32px;font-size:64px;color:var(--red)">Mother’s Day</div>
  <div class="t bold" style="left:59px;top:112px;font-size:57px">SPRING DETOX</div>
  <div style="position:absolute;left:61px;top:184px;width:338px;height:206px;border-radius:22px;background:var(--pink-box)"></div>
  <div class="t semi" style="right:80px;top:186px;font-size:88px">Sale</div>
  <div class="deal" style="--n:205px;left:80px;top:276px;color:var(--red)"><span class="num">25</span><span class="side"><span class="sym">%</span><span class="off">OFF</span></span></div>
  <div class="t semi" style="left:61px;top:457px;font-size:58px">Everything!</div>
</section>

<!-- 2 -->
<section class="post col-b row-1">
  <div class="photo" role="img" aria-label="Smiling woman in a white cropped sweater presenting the supplement range" style="left:290px;top:102px;width:170px;height:473px"></div>
  <div class="bottles" role="img" aria-label="Row of Liver Bloom, Tummy Bloom, Sugar Bloom and Hormone Bloom bottles" style="left:215px;top:450px;width:245px;height:125px"></div>
  <div class="deal" style="--n:176px;left:33px;top:46px;color:var(--plum)"><span class="num">25</span><span class="side"><span class="sym">%</span><span class="off">OFF</span></span></div>
  <div class="t semi" style="left:31px;top:208px;font-size:45px">MOTHER’S DAY</div>
  <div class="t reg" style="left:29px;top:312px;font-size:57px;color:var(--plum)">Spring Detox</div>
  <div class="t bold" style="left:29px;top:372px;font-size:100px">SALE</div>
</section>

<!-- 3 -->
<section class="post col-a row-2">
  <div class="deal" style="--n:183px;left:35px;top:32px;color:var(--blue)"><span class="num">25</span><span class="side"><span class="sym">%</span><span class="off">OFF</span></span></div>
  <div class="t" style="left:37px;top:200px;font-family:'Montserrat',sans-serif;font-weight:500;font-size:28px">All Supplements</div>
  <div class="t bold" style="left:35px;top:239px;font-size:56px;color:var(--blue)">SPRING DETOX</div>
  <div class="bottles" role="img" aria-label="Sugar Bloom, Hormone Bloom, Tummy Bloom and Liver Bloom bottles" style="left:30px;top:331px;width:318px;height:187px"></div>
  <div class="t bold" style="left:355px;top:522px;font-size:88px;transform:rotate(-90deg);transform-origin:0 0">SALE!</div>
</section>

<!-- 4 -->
<section class="post col-b row-2">
  <div class="deal" style="--n:194px;right:26px;top:13px;color:var(--forest)"><span class="num">25</span><span class="side"><span class="sym">%</span><span class="off">OFF</span></span></div>
  <div class="bottles" role="img" aria-label="Liver Bloom, Tummy Bloom, Hormone Bloom and Sugar Bloom bottles" style="left:30px;top:191px;width:405px;height:176px"></div>
  <div class="t" style="right:25px;top:368px;font-size:0">
    <span class="semi" style="font-size:44px;color:var(--forest)">Spring Detox </span><span class="bold" style="font-size:67px;color:var(--red)">SALE</span>
  </div>
  <div class="t semi" style="right:25px;top:451px;font-size:38px;color:var(--forest)">Spring Reset</div>
  <div class="t semi" style="right:25px;top:497px;font-size:38px;color:var(--forest)">Summer Ready</div>
</section>

<!-- 5 -->
<section class="post col-a row-3">
  <div class="photo" role="img" aria-label="Smiling woman in a white cropped sweater with the supplement bottles" style="left:295px;top:0;width:165px;height:281px"></div>
  <div class="bottles" role="img" aria-label="Row of supplement bottles" style="left:255px;top:220px;width:205px;height:61px"></div>
  <div class="deal" style="--n:157px;left:37px;top:56px;color:var(--red)"><span class="num">25</span><span class="side"><span class="sym">%</span><span class="off">OFF</span></span></div>
  <div class="t light" style="left:36px;top:202px;font-size:47px">Everything</div>
  <div class="band" style="top:280px;height:93px;background:var(--pink-band)"></div>
  <div class="t semi" style="left:36px;top:293px;font-size:52px;color:var(--maroon)">Mother’s Day</div>
  <div class="t bold" style="left:35px;top:382px;font-size:61px;color:var(--red)">SPRING DETOX</div>
  <div class="t bold" style="left:33px;top:452px;font-size:89px">Sale</div>
</section>

<!-- 6 -->
<section class="post col-b row-3">
  <div class="photo" role="img" aria-label="Smiling woman in a white cropped sweater presenting the supplement range" style="left:0;top:15px;width:240px;height:390px"></div>
  <div class="deal" style="--n:127px;left:249px;top:51px;color:var(--rose)"><span class="num">25</span><span class="side"><span class="sym">%</span><span class="off">OFF</span></span></div>
  <div class="t semi" style="left:249px;width:190px;text-align:center;top:165px;font-size:45px">MOTHER’S</div>
  <div class="t semi" style="left:249px;width:190px;text-align:center;top:222px;font-size:45px">DAY</div>
  <div class="t semi" style="left:249px;width:190px;text-align:center;top:283px;font-size:66px;color:var(--rose)">SALE</div>
  <div class="band" style="top:404px;height:102px;background:var(--rose)"></div>
  <div class="t semi center" style="top:437px;font-size:44px;color:var(--white)">FEEL AMAZING AGAIN!</div>
</section>

<!-- 7 -->
<section class="post col-a row-4">
  <svg style="position:absolute;left:0;top:0" width="460" height="575" aria-hidden="true"><circle cx="478" cy="215" r="175" fill="var(--violet)"/></svg>
  <div class="deal" style="--n:164px;left:53px;top:36px;color:var(--violet)"><span class="num">25</span><span class="side"><span class="sym">%</span><span class="off">OFF</span></span></div>
  <div class="bottles" role="img" aria-label="Sugar Bloom, Hormone Bloom, Tummy Bloom and Liver Bloom bottles" style="left:99px;top:197px;width:361px;height:212px"></div>
  <div class="t" style="left:34px;top:414px;font-size:0">
    <span class="semi" style="font-size:46px;color:var(--violet)">Mother’s Day </span><span class="bold" style="font-size:71px;color:var(--red)">SALE</span>
  </div>
  <div class="t semi" style="left:34px;top:493px;font-size:45px">REFRESH YOUR BODY</div>
</section>

<!-- 8 -->
<section class="post col-b row-4">
  <div class="band" style="top:0;height:179px;background:var(--mint)"></div>
  <div class="deal" style="--n:142px;left:122px;top:22px;color:var(--ink)"><span class="num">25</span><span class="side"><span class="sym">%</span><span class="off">OFF</span></span></div>
  <div class="bottles" role="img" aria-label="Liver Bloom, Tummy Bloom, Hormone Bloom and Sugar Bloom bottles" style="left:30px;top:155px;width:405px;height:170px"></div>
  <div class="t center" style="top:343px;font-size:53px"><span class="light">SPRING DETOX </span><span class="bold">SALE</span></div>
  <div class="t bold center" style="top:413px;font-size:50px;color:var(--mint-text)">SPRING CLEANSE.</div>
  <div class="t bold center" style="top:476px;font-size:51px">SUMMER GLOW</div>
</section>

<!-- 9 -->
<section class="post col-a row-5">
  <div class="photo" role="img" aria-label="Smiling woman in a white cropped sweater with the supplement bottles" style="left:295px;top:67px;width:165px;height:231px"></div>
  <div class="deal" style="--n:164px;left:29px;top:53px;color:var(--red)"><span class="num">25</span><span class="side"><span class="sym">%</span><span class="off">OFF</span></span></div>
  <div class="t bold" style="left:28px;top:203px;font-size:73px">Mother’s</div>
  <div class="t bold" style="left:28px;top:297px;font-size:73px">Day</div>
  <div style="position:absolute;left:154px;top:298px;width:306px;height:76px;border-radius:38px 0 0 38px;background:var(--red)"></div>
  <div class="t bold" style="left:194px;top:301px;font-size:70px;color:var(--white)">Sale</div>
  <div class="t light" style="left:28px;top:386px;font-size:62px">Detox This Spring.</div>
  <div class="t bold" style="left:28px;top:460px;font-size:49px">Shine This Summer</div>
</section>

<!-- 10 -->
<section class="post col-b row-5">
  <div class="band" style="top:136px;height:236px;background:var(--plum)"></div>
  <div class="bottles" role="img" aria-label="Liver Bloom, Tummy Bloom, Hormone Bloom and Sugar Bloom bottles" style="left:45px;top:24px;width:375px;height:152px"></div>
  <div class="deal" style="--n:190px;left:92px;top:184px;color:var(--white)"><span class="num">25</span><span class="side"><span class="sym">%</span><span class="off">OFF</span></span></div>
  <div class="t semi center" style="top:383px;font-size:53px;color:var(--plum)">Mother’s Day Sale</div>
  <div class="t light center" style="top:447px;font-size:45px">Spring Detox for a</div>
  <div class="t bold center" style="top:497px;font-size:47px">Summer Body</div>
</section>

</body>
</html>
```